Business Cards Needed for Innovative Healthcare Marketing Company

We are a marketing company focused on healthcare. Our company is all about rebranding yourself renewing your image and generating results. The phoenix stands for "reborn" or "rising" which we provide new brands for our clients we take their old brands and renew it with creativity and innovation. I am looking for a business card with color dimension. I have attached an example of a card I think has the look and feel of what I am trying to accomplish. I like that the card example has black and grey font colors, I like the font placement and the small logo, I really like the use of the colors on the right those are the colors of my logo. My logo is phoenix so maybe incorporating flames similar to that design. I would like the back a solid color maybe red with an opaque version of the logo and website. As a marketing company I am always open to creative liberty!

Target Market(s)

Doctors and business professionals.

Industry/Entity Type

Marketing

Contact Information for Business Card

Valcorne Health Care Marketing
Marla Tenwick- CEO
#(512)638-2974
email-marla@valcorne.com
website- valcorne.com

Font styles to use
Sans Serif

Colors
ec1f27
f37122
ffc214
fbed22
fbf289
f04a50

Requirements
Must have
• The logo and required information
Nice to have
• icons by the information
Should not have
• child like font

```html
<!DOCTYPE html>
<html lang="en">
<head>
<meta charset="utf-8">
<title>Valcorne Health Care Marketing – Business Card</title>
<link rel="stylesheet" href="https://fonts.googleapis.com/css2?family=Open+Sans:wght@300;400&display=swap">
<style>
  :root {
    --red: #ec1f27;
    --red-deep: #b8161c;
    --red-soft: #f04a50;
    --orange: #f37122;
    --yellow: #ffc214;
    --ink: #333333;
    --ink-soft: #555555;
    --paper: #ffffff;
    --backdrop: #ecebe8;
  }
  * { box-sizing: border-box; margin: 0; padding: 0; }
  html, body {
    width: 780px; height: 1200px; overflow: hidden;
    background: var(--backdrop);
    font-family: "Open Sans", Arial, sans-serif;
  }
  .sheet { position: relative; width: 780px; height: 1200px; }
  .card {
    position: absolute; left: 70px; width: 640px; height: 366px;
    border-radius: 4px; overflow: hidden;
    box-shadow: 0 10px 30px rgba(0,0,0,.18);
  }
  .card--front { top: 90px; background: var(--paper); }
  .card--back {
    top: 700px;
    background: linear-gradient(160deg, var(--red-soft) 0%, var(--red) 45%, var(--red-deep) 100%);
  }
  .front-band {
    position: absolute; left: 0; top: 0; width: 640px; height: 150px;
    background: linear-gradient(90deg, var(--red) 0%, var(--red-soft) 35%, var(--orange) 65%, var(--yellow) 100%);
  }
  .brand {
    position: absolute; left: 34px; top: 196px; width: 190px;
    display: flex; align-items: center; gap: 10px;
  }
  .brand-dot { width: 20px; height: 20px; border-radius: 50%; background: var(--orange); flex: none; }
  .brand-name { font-weight: 400; font-size: 13px; line-height: 17px; color: var(--red); letter-spacing: .5px; }
  .person { position: absolute; left: 250px; top: 178px; }
  .person-name { font-weight: 400; font-size: 28px; line-height: 36px; color: var(--ink); }
  .person-title { font-weight: 400; font-size: 16px; line-height: 22px; color: var(--red); }
  .contacts { list-style: none; margin-top: 12px; }
  .contacts li {
    display: flex; align-items: center; gap: 10px;
    font-size: 14px; color: var(--ink-soft); line-height: 26px;
  }
  .icon { width: 16px; height: 16px; flex: none; }
  .back-mark {
    position: absolute; left: 110px; top: 120px;
    display: flex; align-items: center; gap: 26px;
  }
  .back-circle {
    width: 90px; height: 90px; border-radius: 50%;
    background: rgba(255,255,255,.16);
  }
  .back-name { color: rgba(255,255,255,.38); font-weight: 300; }
  .back-name-main { font-size: 64px; letter-spacing: 4px; line-height: 1; }
  .back-rule { height: 1px; background: rgba(255,255,255,.38); margin: 8px 0 6px; }
  .back-name-sub { font-size: 17px; letter-spacing: 3px; }
</style>
</head>
<body>
<main class="sheet">
  <section class="card card--front" aria-label="Card front">
    <div class="front-band" role="img" aria-label="Decorative warm flame-coloured graphic in red, orange and yellow"></div>

    <div class="brand">
      <span class="brand-dot"></span>
      <span class="brand-name">VALCORNE HEALTH CARE MARKETING</span>
    </div>

    <div class="person">
      <p class="person-name">Marla Tenwick</p>
      <p class="person-title">CEO</p>
      <ul class="contacts">
        <li>
          <svg class="icon" viewBox="0 0 16 16"><rect width="16" height="16" rx="3" fill="var(--red)"/><path d="M5 4c1 0 1.5 2 1 2.5s0 2 1.5 3.5 3 2 3.5 1.5 2.5 0 2.5 1-1.5 1.5-2.5 1.5C7 14 2 9 2 5.5 2 4.5 4 4 5 4z" fill="#fff" transform="scale(.85) translate(1.5 0)"/></svg>
          (512)638-2974
        </li>
        <li>
          <svg class="icon" viewBox="0 0 16 16"><rect width="16" height="16" rx="3" fill="var(--red)"/><rect x="3" y="5" width="10" height="7" fill="#fff"/><path d="M3 5l5 4 5-4" stroke="var(--red)" stroke-width="1.2" fill="none"/></svg>
          email- marla@valcorne.com
        </li>
        <li>
          <svg class="icon" viewBox="0 0 16 16"><circle cx="8" cy="8" r="7" fill="var(--red)"/><circle cx="8" cy="8" r="4.5" fill="none" stroke="#fff" stroke-width="1"/><path d="M3.5 8h9M8 3.5c-2 2.5-2 6.5 0 9M8 3.5c2 2.5 2 6.5 0 9" stroke="#fff" stroke-width="1" fill="none"/></svg>
          website- valcorne.com
        </li>
      </ul>
    </div>
  </section>

  <section class="card card--back" aria-label="Card back">
    <div class="back-mark">
      <span class="back-circle"></span>
      <div class="back-name">
        <p class="back-name-main">VALCORNE</p>
        <div class="back-rule"></div>
        <p class="back-name-sub">HEALTH CARE MARKETING</p>
      </div>
    </div>
  </section>
</main>
</body>
</html>
```